Podiatry (services) Business Card

I need a business design for a New Podiatry Service.
the Podiatry services will include all aspects of podiatry including;
general podiatry for all ages
corns and callus treatment
Ingrown toenails & nail surgery
Forefoot, arch and heel pain
Gait analysis
Sports Podiatry and Orthotics
Paediatric Assessments
Diabetes Foot Assessment

I would like the back of the card to have space for next appointment day and time.

I would like a nice design that is simple yet catchy. I don't like cluttered business cards. I like things to be simple yet stand out because of the finer details.

I like the colours blue and white but I'm open to other designs that have different colours.

Business

Bluewren Podiatry (Business name)

Marisol Tenbury - Podiatrist
M.Pod.P., B.Hlth. Sci, MFLsoc

Address: 58 Coleby St, Marrowdale North Vic, 3164
Phone: (03) 9416 2738
Fax: (03) 9523 4178

```html
<!DOCTYPE html>
<html lang="en">
<head>
<meta charset="utf-8">
<title>Bluewren Podiatry – Business Card</title>
<link href="https://fonts.googleapis.com/css2?family=Open+Sans:wght@400;600;700&display=swap" rel="stylesheet">
<style>
  :root {
    --blue: #0a78c8;
    --blue-dark: #0767ad;
    --ink: #1e1e1e;
    --paper: #ffffff;
    --paper-grey: #eceef0;
    --backdrop: #e4e6e9;
  }
  * { box-sizing: border-box; margin: 0; padding: 0; }
  html, body {
    width: 1200px; height: 900px; overflow: hidden;
    background: var(--backdrop);
    font-family: "Open Sans", Arial, sans-serif;
  }
  .sheet {
    width: 1200px; height: 900px;
    display: flex; flex-direction: column;
    align-items: center; justify-content: center; gap: 40px;
  }
  .card {
    position: relative;
    width: 700px; height: 400px;
    background: var(--paper);
    box-shadow: 0 4px 14px rgba(0,0,0,.18);
    overflow: hidden;
  }

  /* ---------- Front ---------- */
  .corner-mark { position: absolute; left: 0; top: 14px; width: 52px; height: 46px; }
  .identity { position: absolute; left: 78px; top: 16px; }
  .identity .name { font-size: 22px; font-weight: 700; color: var(--blue); }
  .identity .role { font-size: 16px; font-weight: 400; color: var(--ink); }
  .identity .credentials { font-size: 14px; color: var(--ink); margin-top: 2px; }
  .contact { position: absolute; left: 30px; top: 160px; font-size: 15px; color: var(--ink); line-height: 1.45; }
  .contact .address { margin-bottom: 14px; }
  .contact .line { display: flex; align-items: center; gap: 8px; }
  .contact svg { width: 13px; height: 13px; fill: var(--blue); }
  .brand {
    position: absolute; left: 330px; top: 175px;
    display: flex; align-items: center; gap: 14px;
  }
  .brand-dot { width: 34px; height: 34px; border-radius: 50%; background: var(--blue); }
  .brand-name {
    font-size: 34px; font-weight: 600; color: var(--blue);
    letter-spacing: 1px; text-transform: uppercase; line-height: 1.05;
  }
  .brand-rule { position: absolute; left: 330px; top: 262px; width: 340px; height: 1px; background: var(--blue); }
  .bottom-band { position: absolute; left: 0; bottom: 0; width: 700px; height: 90px; }

  /* ---------- Back ---------- */
  .card.back { background: linear-gradient(135deg, #f4f5f6 0%, var(--paper-grey) 100%); }
  .services {
    position: absolute; left: 0; right: 0; top: 40px;
    list-style: none; text-align: center;
    font-size: 15px; font-weight: 600; color: var(--blue);
    text-transform: uppercase; line-height: 1.3;
  }
  .appointment-title {
    position: absolute; left: 0; right: 0; top: 250px; text-align: center;
    font-size: 24px; font-weight: 700; color: var(--blue-dark);
    text-decoration: underline; text-underline-offset: 4px;
  }
  .appointment-fields { position: absolute; left: 40px; right: 40px; top: 300px; font-size: 15px; font-weight: 600; color: var(--blue); }
  .field { display: flex; align-items: baseline; gap: 6px; }
  .field .fill { flex: 1; border-bottom: 2px dotted var(--ink); height: 1em; }
  .field-row { display: flex; gap: 24px; margin-top: 18px; }
  .field-row .field { flex: 1; }
</style>
</head>
<body>
<main class="sheet">

  <!-- Front of card -->
  <section class="card front">
    <svg class="corner-mark" viewBox="0 0 52 46" aria-hidden="true">
      <rect width="52" height="46" fill="var(--blue)"/>
      <line x1="14" y1="44" x2="50" y2="4" stroke="#fff" stroke-width="3"/>
    </svg>

    <div class="identity">
      <p><span class="name">Marisol Tenbury</span> <span class="role">- Podiatrist</span></p>
      <p class="credentials">M.Pod.P, B.Hlth. Sci, MFLsoc</p>
    </div>

    <div class="contact">
      <p class="address">58 Coleby St, Marrowdale<br>North Vic, 3164</p>
      <p class="line">
        <svg viewBox="0 0 24 24" aria-hidden="true"><path d="M6.6 10.8a15.1 15.1 0 0 0 6.6 6.6l2.2-2.2a1 1 0 0 1 1-.25 11.4 11.4 0 0 0 3.6.57 1 1 0 0 1 1 1V20a1 1 0 0 1-1 1A17 17 0 0 1 3 4a1 1 0 0 1 1-1h3.5a1 1 0 0 1 1 1c0 1.25.2 2.45.57 3.6a1 1 0 0 1-.25 1z"/></svg>
        (03) 9416 2738
      </p>
      <p class="line">
        <svg viewBox="0 0 24 24" aria-hidden="true"><path d="M6 2h9v5H6zM4 8h16a1 1 0 0 1 1 1v12a1 1 0 0 1-1 1H4a1 1 0 0 1-1-1V9a1 1 0 0 1 1-1zm3 4v2h4v-2zm0 4v2h4v-2zm7-4v6h3v-6z"/></svg>
        (03) 9523 4178
      </p>
    </div>

    <div class="brand">
      <span class="brand-dot"></span>
      <span class="brand-name">Bluewren<br>Podiatry</span>
    </div>
    <div class="brand-rule"></div>

    <svg class="bottom-band" viewBox="0 0 700 90" aria-hidden="true">
      <polygon points="0,40 250,40 232,58 0,58" fill="var(--blue)"/>
      <polygon points="262,40 700,40 700,90 212,90" fill="var(--blue)"/>
    </svg>
  </section>

  <!-- Back of card -->
  <section class="card back">
    <ul class="services">
      <li>General podiatry for all ages</li>
      <li>Corns and callus treatment</li>
      <li>Ingrown toenails &amp; nail surgery</li>
      <li>Forefoot, arch and heel pain</li>
      <li>Gait analysis</li>
      <li>Sports podiatry and orthotics</li>
      <li>Paediatric assessments</li>
      <li>Diabetes foot assessment</li>
    </ul>

    <h2 class="appointment-title">Appointment</h2>

    <div class="appointment-fields">
      <div class="field"><span>Name:</span><span class="fill"></span></div>
      <div class="field-row">
        <div class="field"><span>Date:</span><span class="fill"></span></div>
        <div class="field"><span>Time:</span><span class="fill"></span></div>
      </div>
    </div>
  </section>

</main>
</body>
</html>
```